One of a Kind Clean Business Card

We need to design a new business card template for our company. Our company designs and produced merchandising displays. You can see a sample of what we produce on our site www.qorvanexhibits.net. I have uploaded our logo in vector format, as well as a picture of our current business cards. We want a totally different look. We want simple and clean, looking forward to seeing what people create.
Updates

I would like to update the address for Qorvan Display Group Inc. 518 E Tollmere Ln Arlington Heights, IL 60017 Would also note. No QR codes

Industry/Entity Type

Business

Contact Information for Business Card

Need a 1 sided business card designed.

Font styles to use
Serif

Requirements
Must have
• Easy to view; Clean Design
Nice to have
• Features that promote engineering and creativity
Should not have
• Too much clutter, keep it simple

```html
<!DOCTYPE html>
<html lang="en">
<head>
<meta charset="utf-8">
<title>Qorvan Display Group Inc. — Business Card</title>
<link rel="stylesheet" href="https://fonts.googleapis.com/css2?family=Lora:wght@400;700&display=swap">
<style>
  :root {
    --backdrop: #2b2b2b;
    --card: #f7f7f7;
    --ink: #1e1e1e;
    --muted: #555555;
    --accent: #8c1c1c;
    --frame: #111111;
  }
  html, body {
    margin: 0;
    width: 1200px;
    height: 997px;
    overflow: hidden;
    background: var(--backdrop);
  }
  .stage {
    position: relative;
    width: 1200px;
    height: 997px;
  }
  .business-card {
    position: absolute;
    left: 150px;
    top: 241px;
    width: 900px;
    height: 514px;
    border-radius: 28px;
    background: linear-gradient(135deg, #ffffff 0%, var(--card) 55%, #ececec 100%);
    overflow: hidden;
    font-family: "Lora", Georgia, serif;
    color: var(--ink);
  }
  .product-tiles {
    position: absolute;
    inset: 0;
  }
  .brand {
    position: absolute;
    left: 490px;
    top: 50px;
    display: flex;
    align-items: center;
    gap: 12px;
  }
  .brand-mark {
    width: 16px;
    height: 16px;
    background: var(--accent);
  }
  .brand-name {
    font-size: 24px;
    font-weight: 400;
    color: var(--accent);
    letter-spacing: 0.3px;
    white-space: nowrap;
  }
  .brand-rule {
    position: absolute;
    left: 490px;
    top: 96px;
    width: 370px;
    height: 2px;
    background: var(--ink);
  }
  .holder {
    position: absolute;
    right: 70px;
    top: 114px;
    text-align: right;
  }
  .holder-name {
    font-size: 22px;
    font-weight: 700;
    letter-spacing: 0.5px;
  }
  .holder-role {
    font-size: 17px;
    color: var(--accent);
    margin-top: 2px;
  }
  .contact-list {
    position: absolute;
    right: 40px;
    top: 250px;
    margin: 0;
    padding: 0;
    list-style: none;
    font-size: 18px;
    line-height: 28px;
  }
  .contact-list li {
    display: flex;
    justify-content: flex-end;
    align-items: center;
    gap: 10px;
  }
  .contact-list svg {
    width: 15px;
    height: 15px;
  }
  .contact-email {
    position: absolute;
    right: 40px;
    top: 346px;
    font-size: 18px;
    white-space: nowrap;
  }
  .contact-address {
    position: absolute;
    right: 40px;
    top: 378px;
    font-size: 14px;
    color: var(--muted);
    white-space: nowrap;
  }
  .website {
    position: absolute;
    right: 40px;
    top: 430px;
    font-size: 20px;
    font-weight: 700;
    color: var(--accent);
    letter-spacing: 0.3px;
  }
</style>
</head>
<body>
<main class="stage">
  <section class="business-card">
    <svg class="product-tiles" width="900" height="514" viewBox="0 0 900 514">
      <defs>
        <linearGradient id="tile-shelf" x1="0" y1="0" x2="1" y2="1">
          <stop offset="0" stop-color="#3a5a8a"/>
          <stop offset="0.5" stop-color="#3f6e4e"/>
          <stop offset="1" stop-color="#8a5a3a"/>
        </linearGradient>
        <linearGradient id="tile-case" x1="0" y1="0" x2="1" y2="1">
          <stop offset="0" stop-color="#f3f3f3"/>
          <stop offset="0.5" stop-color="#b82020"/>
          <stop offset="1" stop-color="#f3f3f3"/>
        </linearGradient>
        <linearGradient id="tile-barrel" x1="0" y1="0" x2="0" y2="1">
          <stop offset="0" stop-color="#f3f3f3"/>
          <stop offset="0.5" stop-color="#c49a6a"/>
          <stop offset="1" stop-color="#a47a4a"/>
        </linearGradient>
      </defs>
      <g role="img" aria-label="Photo of a tiered cardboard shelf display">
        <rect x="-90" y="-90" width="240" height="240" rx="40" transform="rotate(45 30 30)" fill="#ffffff" stroke="var(--frame)" stroke-width="3"/>
        <ellipse cx="110" cy="70" rx="90" ry="50" fill="url(#tile-shelf)" opacity="0.85"/>
      </g>
      <g role="img" aria-label="Photo of a red countertop product display">
        <rect x="185" y="120" width="230" height="230" rx="40" transform="rotate(45 300 235)" fill="#ffffff" stroke="var(--frame)" stroke-width="3"/>
        <ellipse cx="300" cy="240" rx="80" ry="55" fill="url(#tile-case)" opacity="0.9"/>
      </g>
      <g role="img" aria-label="Photo of a wooden barrel display holding bottles">
        <rect x="30" y="350" width="240" height="240" rx="40" transform="rotate(45 150 470)" fill="#ffffff" stroke="var(--frame)" stroke-width="3"/>
        <rect x="70" y="380" width="160" height="134" rx="20" fill="url(#tile-barrel)"/>
      </g>
    </svg>

    <div class="brand">
      <span class="brand-mark"></span>
      <span class="brand-name">Qorvan Display Group Inc.</span>
    </div>
    <div class="brand-rule"></div>

    <div class="holder">
      <div class="holder-name">DARREN HOLLIS</div>
      <div class="holder-role">Co-Founder</div>
    </div>

    <ul class="contact-list">
      <li>+44 207 555 0148
        <svg viewBox="0 0 16 16"><rect x="4" y="1" width="8" height="14" rx="1.5" fill="none" stroke="var(--accent)" stroke-width="1.6"/></svg>
      </li>
      <li>07700 900318
        <svg viewBox="0 0 16 16"><rect x="1" y="3" width="14" height="10" fill="var(--accent)"/><path d="M1 3 L8 9 L15 3" fill="none" stroke="#fff" stroke-width="1.2"/></svg>
      </li>
      <li>qorvanexhibits.net
        <svg viewBox="0 0 16 16"><path d="M6 10 L10 6 M7 4 L9 2 a3 3 0 0 1 5 5 L12 9 M9 12 L7 14 a3 3 0 0 1 -5 -5 L4 7" fill="none" stroke="var(--accent)" stroke-width="1.6"/></svg>
      </li>
    </ul>
    <div class="contact-email">m.ashford@qorvanexhibits.net</div>
    <div class="contact-address">518 E Tollmere Ln Arlington Heights, IL 60017</div>
    <div class="website">www.qorvanexhibits.net</div>
  </section>
</main>
</body>
</html>
```